Meridale Real Estate

We are looking for help with web design for a new company that is revolutionizing the real estate world on the listing side: by charing per hour for top level professional real estate services. We would like the concept to be simple, clean and easily understood.
Updates

We want this website to actually function, not just a static design.

Industry/Entity Type

Real Estate

```html
<!DOCTYPE html>
<html lang="en">
<head>
<meta charset="utf-8">
<title>Meridale Real Estate</title>
<link rel="stylesheet" href="https://fonts.googleapis.com/css2?family=Arimo:wght@400;700&display=swap">
<style>
:root{
  --blue:#0a7fd4;
  --blue-dark:#0563b4;
  --blue-light:#27a9ee;
  --red:#e41f1f;
  --red-dark:#b80d0d;
  --text:#3a3a3a;
  --muted:#555;
  --panel:#f1f2f4;
  --line:#d9dde2;
  --white:#fff;
  --hero-a:#6d8fbf;
  --hero-b:#8c948c;
  --photo-a1:#88a592;
  --photo-a2:#a8b2a6;
  --photo-b1:#9db1c9;
  --photo-b2:#c8c2b2;
}
*{box-sizing:border-box;margin:0;padding:0}
html,body{width:1169px;height:1200px;overflow:hidden}
body{font-family:"Arimo",Arial,sans-serif;color:var(--text);background:var(--white)}
.canvas{position:relative;width:1169px;height:1200px;overflow:hidden;
  background:linear-gradient(#eef0f3 0,#f8f9fa 172px,#f3f4f6 575px,#e9ebee 1200px)}
.abs{position:absolute}

/* header */
.brand{left:126px;top:44px;display:flex;align-items:center;gap:8px;font-size:17px;font-weight:700;color:var(--blue)}
.brand-dot{width:14px;height:14px;border-radius:50%;background:var(--blue)}
.phone{right:125px;top:55px;font-size:17px;color:var(--blue)}
.phone span{color:var(--red)}

.nav{left:124px;top:109px;width:922px;height:46px;display:flex;border-radius:4px;
  background:linear-gradient(var(--blue-light),var(--blue-dark));overflow:hidden;box-shadow:0 1px 2px rgba(0,0,0,.2)}
.nav a{display:flex;align-items:center;justify-content:center;color:var(--white);text-decoration:none;
  font-size:17px;font-weight:700;border-left:1px solid rgba(255,255,255,.25)}
.nav a:first-child{border-left:0}
.nav a.is-active{background:linear-gradient(#f23030,var(--red-dark))}

/* hero */
.hero-band{left:0;top:172px;width:1169px;height:403px;
  background:linear-gradient(90deg,#0b7fd0,#1c9ae6 45%,#5cc4f3 100%)}
.hero-frame{left:124px;top:191px;width:924px;height:363px;background:var(--white);box-shadow:0 2px 6px rgba(0,0,0,.25)}
.hero-photo{left:11px;top:9px;width:901px;height:343px;
  background:linear-gradient(160deg,var(--hero-a),var(--hero-b))}
.slider-dots{left:760px;top:324px;width:114px;height:31px;border-radius:8px 8px 0 0;
  background:linear-gradient(var(--blue-light),var(--blue-dark));display:flex;gap:4px;align-items:center;justify-content:center}
.slider-dots i{width:11px;height:11px;border-radius:50%;background:#c9e6f8;border:1px solid #0a5a9c}
.slider-dots i.is-on{background:var(--white)}

/* content panel */
.main{left:124px;top:575px;width:924px;height:543px;background:var(--white);border-radius:0 0 8px 8px;box-shadow:0 1px 3px rgba(0,0,0,.15)}
.welcome-title{left:137px;top:590px;font-size:21px;font-weight:400;color:#222}
.welcome-title strong{font-size:16px;color:var(--blue);letter-spacing:.3px}
.welcome-text{left:137px;width:594px;font-size:13.5px;line-height:16px;color:var(--text)}
.welcome-text span{display:block;text-align:justify;text-align-last:justify;white-space:nowrap}
.welcome-text span:last-child{text-align-last:left}

.section-title{font-size:21px;font-weight:400;color:var(--blue)}
.pager{display:flex;gap:3px}
.pager span{width:21px;height:21px;border-radius:50%;border:1px solid #aaa;background:linear-gradient(#fff,#ddd);
  display:flex;align-items:center;justify-content:center}

.listings{left:135px;top:842px;width:597px;height:258px;display:flex;gap:1px;background:var(--line)}
.listing{position:relative;flex:1;background:linear-gradient(#fbfbfb,#e9eaec);padding:10px 13px}
.listing-photo{position:relative;width:174px;height:110px;background:var(--white);border:1px solid #ccc;padding:4px}
.listing-photo .fill{width:100%;height:100%}
.tone-a{background:linear-gradient(160deg,var(--photo-a1),var(--photo-a2))}
.tone-b{background:linear-gradient(160deg,var(--photo-b1),var(--photo-b2))}
.sold-tag{position:absolute;left:-4px;top:-2px}
.listing-name{margin-top:4px;font-size:17px;color:#111}
.listing-row{font-size:16px;color:#111;display:flex}
.listing-row b{font-weight:400;width:76px}
.listing-row .price{color:var(--red)}
.listing-desc{margin-top:4px;font-size:12px;line-height:14px;text-align:justify;color:var(--text)}
.listing-more{position:absolute;right:12px;bottom:6px;font-size:12px;color:var(--blue-dark)}

/* search */
.search{left:757px;top:586px;width:278px;height:253px;background:var(--panel);border:1px solid #e2e4e7;border-radius:4px}
.search-title{position:absolute;left:14px;top:10px;font-size:21px;font-weight:400;color:var(--blue)}
.field{position:absolute;width:114px;font-size:14px;color:var(--text)}
.field select{display:block;margin-top:4px;width:114px;height:22px;appearance:none;-webkit-appearance:none;
  border:1px solid #b6bcc4;background:linear-gradient(90deg,#fff 0,#fff 92px,#cfe3f6 92px);font:inherit;color:var(--text)}
.field .arrow{position:absolute;right:4px;bottom:6px}
.btn-search{position:absolute;left:152px;top:210px;width:105px;height:28px;border:0;border-radius:5px;
  background:linear-gradient(#f43a3a,var(--red-dark));color:var(--white);font:700 16px "Arimo",Arial,sans-serif}

/* news */
.news-text{left:758px;width:277px;font-size:13px;line-height:16px;color:var(--text);white-space:nowrap}
.news-more{right:134px;font-size:14px;color:var(--red)}
.news-rule{left:758px;top:992px;width:277px;border-top:1px dotted #888}

/* footer */
.footer-nav{left:0;width:1169px;top:1138px;text-align:center;font-size:14px;color:var(--muted)}
.copyright{left:0;width:1169px;top:1161px;text-align:center;font-size:10px;font-weight:700;color:var(--muted)}
</style>
</head>
<body>
<div class="canvas">

  <div class="abs brand"><span class="brand-dot"></span>Meridale Real Estate</div>
  <div class="abs phone">Phone: <span>(555) 418-2760</span></div>

  <nav class="abs nav">
    <a href="#" class="is-active" style="width:87px">Home</a>
    <a href="#" style="width:117px">About Us</a>
    <a href="#" style="width:143px">Open Houses</a>
    <a href="#" style="width:177px">Calculator / Links</a>
    <a href="#" style="width:135px">Testimonials</a>
    <a href="#" style="width:135px">Latest News</a>
    <a href="#" style="width:128px">Contact Us</a>
  </nav>

  <div class="abs hero-band"></div>
  <div class="abs hero-frame">
    <div class="abs hero-photo" role="img" aria-label="Photo of a brick family house with a front lawn"></div>
    <div class="abs slider-dots"><i></i><i></i><i></i><i></i><i class="is-on"></i></div>
  </div>

  <div class="abs main"></div>

  <h1 class="abs welcome-title">Welcome to <strong>MERIDALE REAL ESTATE</strong></h1>
  <p class="abs welcome-text" style="top:627px">
    <span>Lorem ipsum dolor sit amet, consectetur adipiscing elit. Phasellus justo turpis, sollicitudin sed</span>
    <span>elementum id, dictum et libero. Nulla facilisi. Aliquam mollis justo at nunc interdum fringilla.</span>
    <span>Maecenas porta, libero interdum sagittis vestibulum, tortor lectus lobortis orci, eu porta enim quam</span>
    <span>sed augue. Proin semper mattis felis, porta vehicula odio cursus bibendum. Praesent pharetra justo</span>
    <span>sit amet purus congue porttitor. Donec vel ipsum nec orci sollicitudin aliquam.</span>
  </p>
  <p class="abs welcome-text" style="top:723px">
    <span>Lorem ipsum dolor sit amet, consectetur adipiscing elit. Phasellus justo turpis, sollicitudin sed</span>
    <span>elementum id, dictum et libero. Nulla facilisi. Aliquam mollis justo at nunc interdum fringilla.</span>
    <span>Maecenas porta, libero interdum sagittis vestibulum.</span>
  </p>

  <h2 class="abs section-title" style="left:137px;top:812px">Featured Listings</h2>
  <div class="abs pager" style="left:681px;top:812px">
    <span><svg width="8" height="9"><path d="M7 0L1 4.5 7 9z" fill="#555"/></svg></span>
    <span><svg width="8" height="9"><path d="M1 0L7 4.5 1 9z" fill="#555"/></svg></span>
  </div>

  <div class="abs listings">
    <article class="listing">
      <div class="listing-photo"><div class="fill tone-a" role="img" aria-label="Photo of a two-storey house among trees"></div></div>
      <div class="listing-name">Alder Crest</div>
      <div class="listing-row"><b>Bedroom:</b>4</div>
      <div class="listing-row"><b>Price:</b><span class="price">$130,000</span></div>
      <p class="listing-desc">Lorem ipsum dolor sit amet, consectetur adipiscing elit. Phasellus justo turpis.</p>
      <a class="listing-more">read more...</a>
    </article>
    <article class="listing">
      <div class="listing-photo"><div class="fill tone-b" role="img" aria-label="Photo of a suburban house with a garage"></div></div>
      <div class="listing-name">Wrenfield</div>
      <div class="listing-row"><b>Bedroom:</b>4</div>
      <div class="listing-row"><b>Price:</b><span class="price">$92,500</span></div>
      <p class="listing-desc">Lorem ipsum dolor sit amet, consectetur adipiscing elit. Phasellus justo turpis.</p>
      <a class="listing-more">read more...</a>
    </article>
    <article class="listing">
      <div class="listing-photo">
        <div class="fill tone-b" role="img" aria-label="Photo of a suburban house with a garage, marked sold"></div>
        <svg class="sold-tag" width="62" height="62" aria-hidden="true"><path d="M0 40 L40 0 L58 6 L6 58 Z" fill="var(--red)"/></svg>
      </div>
      <div class="listing-name">Alder Crest</div>
      <div class="listing-row"><b>Bedroom:</b>4</div>
      <div class="listing-row"><b>Price:</b><span class="price">$130,000</span></div>
      <p class="listing-desc">Lorem ipsum dolor sit amet, consectetur adipiscing elit. Phasellus justo turpis.</p>
      <a class="listing-more">read more...</a>
    </article>
  </div>

  <form class="abs search">
    <h2 class="search-title">Find Your Home</h2>
    <label class="field" style="left:14px;top:54px">Location<select><option></option></select>
      <svg class="arrow" width="10" height="7"><path d="M0 0h10L5 7z" fill="#2c6fb5"/></svg></label>
    <label class="field" style="left:147px;top:54px">Rent or Buy<select><option></option><option>Rent</option><option>Buy</option></select>
      <svg class="arrow" width="10" height="7"><path d="M0 0h10L5 7z" fill="#2c6fb5"/></svg></label>
    <label class="field" style="left:14px;top:105px">Bedrooms<select><option></option></select>
      <svg class="arrow" width="10" height="7"><path d="M0 0h10L5 7z" fill="#2c6fb5"/></svg></label>
    <label class="field" style="left:147px;top:105px">Bathrooms<select><option></option></select>
      <svg class="arrow" width="10" height="7"><path d="M0 0h10L5 7z" fill="#2c6fb5"/></svg></label>
    <label class="field" style="left:14px;top:155px">Minimum Price<select><option></option></select>
      <svg class="arrow" width="10" height="7"><path d="M0 0h10L5 7z" fill="#2c6fb5"/></svg></label>
    <label class="field" style="left:147px;top:155px">Maximum Price<select><option></option></select>
      <svg class="arrow" width="10" height="7"><path d="M0 0h10L5 7z" fill="#2c6fb5"/></svg></label>
    <label class="field" style="left:14px;top:206px">Property Type<select><option></option></select>
      <svg class="arrow" width="10" height="7"><path d="M0 0h10L5 7z" fill="#2c6fb5"/></svg></label>
    <button type="submit" class="btn-search">Search</button>
  </form>

  <h2 class="abs section-title" style="left:758px;top:858px">Latest News</h2>
  <p class="abs news-text" style="top:894px">Lorem ipsum dolor sit amet, consectetur adipi-<br>scing elit. Sed et pulvinar metus. Pellentesque<br>sagittis consectetur metus, in posuere mauris<br>iaculis eget.</p>
  <a class="abs news-more" style="top:969px">read more...</a>
  <div class="abs news-rule"></div>
  <p class="abs news-text" style="top:1005px">Lorem ipsum dolor sit amet, consectetur adipi-<br>scing elit. Sed et pulvinar metus. Pellentesque<br>sagittis consectetur metus, in posuere mauris<br>iaculis eget.</p>
  <a class="abs news-more" style="top:1081px">read more...</a>

  <div class="abs footer-nav">Home | About Us | Open Houses | Calculator / Links | Testimonials | Latest News | Contact Us</div>
  <div class="abs copyright">Copyrights 2015 Meridale Real Estate. All Right Reserved</div>

</div>
</body>
</html>
```